Stationery Design Project

We need a stationery design for our Norwegian trucking company. We have existed for about 15 years and our 12 drivers uses relatively new vehicles to transport goods around in northern Norway. Long distance routes with fresh fish og food transport is our main operations.

We have already made alogo that's printed on our trucks. The logo and a picture of our trucks is attached. I think the logo i crappy, but since its already in use, changing it is not an option in this round. Still using a better colour scheme in the overall stationery and more interesting fonts is possible (altso in the logo).

Company details:
Name: Kjelvraket AS
Organisation nr 873 615 309
Post adress: 8642 Raudvik

I like minimalism and simplicity. I am avalibly for questions in normal GMT working hours either here or on mail: ivar@fjordlast.no

Reason: Hi. Im extending the deadline because I needed some time to find a vector file of our logo. Sorry for the inconvenience

Hi, and thanks for all your interest in the project. Some updates:

-          I have decided to commit to using one of the designs. Some designer will get the payment.

-          I have extended the deadline with 24 hours since I needed some time to find our firms vector logo (a slow Swedish man was holding me up)

-          We will not choose a design before the deadline. No need to rush.

-          We have received a lot of great design and think there is a need to specified the product we want to make:

o   Business Card for all our employers. I just need the design and will duplicate with the correct numbers and name myself. The information on should be: Logo, employer’s name, Phone number, email, website, Postal number and address. Use this as a template: logo, Leif Brattvoll, 47382066, Leif@fjordlast.no,, fjordlast.no, 8642 Raudvik. The order and placement of the information is your creative decision.

o   Stickers to put on the goods we travel. On the sticker the should be the following information: Logo, phone number, Tekst and link: Fraktæ av Kjelvraket. Ke du syns? Fjordlast.no/tilbakemelding (this means: Handled by Kjelvraket. What do you think Fjordlast.no/feedback -à the link will be a feedback form). The placement the information and size is your creative decision with some stings: we have been thinking of using Drukko for printing and see that a size about 6x6 cm, 8x5 or something like that. (with 3000 copies our budget is 200 punds). Any suggestions of other suppliers are welcome. Drukko price calculator http://www.drukkolabelhouse.co.uk/digital-litho-printing/printing-labels-tags/stickers/

o   Letterhead with logo, address, phone number and organizational number.

o   Envelopes with logo,address, phone number and organizational number.

Have a nice day.

 

 

• Using the blue colour in the logo and using a similar graphic approch.

```html
<!DOCTYPE html>
<html lang="no">
<head>
<meta charset="utf-8">
<title>Kjelvraket – business cards</title>
<link rel="stylesheet" href="https://fonts.googleapis.com/css2?family=Open+Sans:wght@400;700&family=Tinos:wght@400;700&display=swap">
<style>
  :root {
    --backdrop: #8c8f93;
    --card-white: #ffffff;
    --card-navy: #0b4c9e;
    --card-blue: #0a73b9;
    --brand-blue: #1466b0;
    --label-blue: #1b78c2;
    --ink: #1e1e1e;
    --card-edge: #6c6c6c;
  }
  * { margin: 0; padding: 0; box-sizing: border-box; }
  html, body { width: 1200px; height: 751px; overflow: hidden; }
  body { background: var(--backdrop); position: relative; }

  .card {
    position: absolute;
    width: 525px;
    height: 300px;
    border-radius: 24px;
    overflow: hidden;
  }
  .card--front { left: 50px; top: 52px; background: var(--card-white); border: 1px solid var(--card-edge); }
  .card--back-white { left: 621px; top: 50px; background: var(--card-white); border: 1px solid var(--card-edge); }
  .card--back-navy { left: 50px; top: 388px; background: var(--card-navy); }
  .card--back-blue { left: 621px; top: 388px; background: var(--card-blue); }

  .brand-name {
    position: absolute;
    left: 0; right: 0;
    text-align: center;
    font-family: "Open Sans", sans-serif;
    font-weight: 700;
    font-size: 46px;
    letter-spacing: 0.5px;
    color: var(--brand-blue);
  }
  .card--front .brand-name { top: 76px; }
  .card--back-white .brand-name,
  .card--back-navy .brand-name,
  .card--back-blue .brand-name { top: 122px; }
  .card--back-navy .brand-name,
  .card--back-blue .brand-name { color: var(--card-white); }

  .web {
    position: absolute;
    left: 0; right: 0;
    top: 248px;
    text-align: center;
    font-family: "Open Sans", sans-serif;
    font-size: 17px;
    letter-spacing: 3.4px;
    color: var(--ink);
  }
  .card--back-navy .web, .card--back-blue .web { color: var(--card-white); top: 248px; }

  .contact { position: absolute; left: 0; top: 0; width: 100%; height: 100%; }
  .contact-row { position: absolute; left: 0; display: flex; align-items: center; }
  .contact-label {
    width: 58px; height: 15px;
    background: var(--label-blue);
    color: var(--card-white);
    font-family: "Tinos", serif;
    font-size: 12.5px;
    line-height: 15px;
    text-align: right;
    padding-right: 3px;
  }
  .contact-value {
    margin-left: 7px;
    font-family: "Tinos", serif;
    font-size: 15px;
    color: var(--ink);
  }
  .row-address { top: 174px; }
  .row-phone { top: 211px; }
  .row-email { top: 235px; }
  .row-web { top: 256px; }

  .person-name {
    position: absolute;
    left: 300px; width: 200px;
    top: 210px;
    text-align: center;
    font-family: "Tinos", serif;
    font-weight: 700;
    font-size: 20px;
    color: var(--brand-blue);
  }
</style>
</head>
<body>
  <section class="card card--front">
    <div class="brand-name">Kjelvraket</div>
    <div class="contact">
      <div class="contact-row row-address"><span class="contact-label">Address</span><span class="contact-value">8642 Raudvik</span></div>
      <div class="contact-row row-phone"><span class="contact-label">Phone</span><span class="contact-value">47382066</span></div>
      <div class="contact-row row-email"><span class="contact-label">Email</span><span class="contact-value">Leif@fjordlast.no</span></div>
      <div class="contact-row row-web"><span class="contact-label">Web</span><span class="contact-value">www.fjordlast.no</span></div>
    </div>
    <div class="person-name">Leif Brattvoll</div>
  </section>

  <section class="card card--back-white">
    <div class="brand-name">Kjelvraket</div>
    <div class="web">www.fjordlast.no</div>
  </section>

  <section class="card card--back-navy">
    <div class="brand-name">Kjelvraket</div>
    <div class="web">www.fjordlast.no</div>
  </section>

  <section class="card card--back-blue">
    <div class="brand-name">Kjelvraket</div>
    <div class="web">www.fjordlast.no</div>
  </section>
</body>
</html>
```